Design and Renovation Company Luxury Business Card

I want to create a luxury business card for a Design and Renovation Firm . We will use our current logo. The company name is 528BUILDA. We do not want anything standard. We need a very unique concept.
Please see uploaded inspiration. I really like the textured paper option. I would like the card to be thick with debossing, and/or embossing options. The logo has orange in it but I would like to see the card with and without the orange. I think the orange may make the company feel less high-end. The goal is to elevate the logo not match its vibe per se of the logo. We want something very unique, not standard at all!
I would like a space for :
Logo,
Name,
Position,
Email,
Office number,
Website Address,
Business Address,
Thank you!
Have fun!
Target Market(s)
Home owners Age 35 +
Industry/Entity Type
Design and Renovation
Contact Information for Business Card
Logo, Name, Position, Email, Office number, Website Address, Business Address,.
Colors
Designer to choose colors to be used in the design.
Requirements
Must have
- A luxury designer feel. Must be black or dark grey but open to other luxury ideas.
Nice to have
- Gold, silver, black embossing or debossing. Textured paper design.
Should not have
- A cheap look and feel.

```html
<!DOCTYPE html>
<html lang="en">
<head>
<meta charset="utf-8">
<title>528BUILDA Business Card</title>
<link rel="stylesheet" href="https://fonts.googleapis.com/css2?family=Montserrat:wght@400;500;700&display=swap">
<style>
  :root {
    --backdrop: #9a9a9a;
    --card-white: #ffffff;
    --ink: #111111;
    --accent: #f39422;
    --card-dark: #161616;
    --pattern-mid: #262626;
    --pattern-light: #4a4a4a;
    --name-light: #ffffff;
  }
  * { margin: 0; padding: 0; box-sizing: border-box; }
  html, body {
    width: 1093px; height: 1200px; overflow: hidden;
    background: var(--backdrop);
    font-family: "Montserrat", sans-serif;
  }
  .canvas { position: relative; width: 1093px; height: 1200px; }
  .card {
    position: absolute; left: 264px; width: 597px; height: 364px;
    border-radius: 18px; overflow: hidden;
  }
  .card--front { top: 225px; background: var(--card-white); color: var(--ink); }
  .card--back { top: 616px; background: var(--card-dark); }

  .company-name {
    position: absolute; font-weight: 500; line-height: 1; white-space: nowrap;
  }
  .card--front .company-name {
    left: 62px; top: 190px; font-size: 30px; letter-spacing: 1px; color: var(--ink);
  }
  .card--back .company-name {
    left: 232px; top: 242px; font-size: 40px; letter-spacing: 1.5px; color: var(--name-light);
  }

  .divider {
    position: absolute; left: 299px; top: 115px; width: 2px; height: 165px;
    background: var(--accent);
  }
  .contact { position: absolute; left: 309px; top: 115px; }
  .contact__name { font-size: 23px; font-weight: 700; line-height: 1.1; }
  .contact__role { font-size: 14px; font-weight: 400; margin-top: 4px; }
  .contact__address { font-size: 14px; line-height: 17px; margin-top: 13px; }
  .contact__list { list-style: none; margin-top: 12px; }
  .contact__item { display: flex; align-items: center; gap: 8px; font-size: 14px; height: 23.5px; }
  .contact__icon { width: 13px; height: 13px; flex: none; }

  .pattern-field {
    position: absolute; inset: 0;
    background: linear-gradient(90deg, var(--card-dark) 0%, var(--pattern-mid) 55%, var(--pattern-light) 100%);
  }
</style>
</head>
<body>
<main class="canvas">
  <section class="card card--front" aria-label="Business card front">
    <span class="company-name">528BUILDA</span>
    <span class="divider"></span>
    <div class="contact">
      <h1 class="contact__name">Daniel Hart</h1>
      <p class="contact__role">Managing Director</p>
      <p class="contact__address">415 Linden Park Ave, #112<br>Graniteview, OH 430517</p>
      <ul class="contact__list">
        <li class="contact__item">
          <svg class="contact__icon" viewBox="0 0 16 16" aria-hidden="true"><path fill="#f39422" d="M3.5 1.5l2.4 2.6-1.3 1.7c.9 2 2.5 3.6 4.6 4.6l1.7-1.3 2.6 2.4-1.4 2.2C7 13.4 2.6 9 1.3 2.9z"/><path fill="none" stroke="#f39422" stroke-width="1.3" d="M9.5 2.5a4 4 0 0 1 4 4M9.5 5a1.5 1.5 0 0 1 1.5 1.5"/></svg>
          <span>555-318-2740</span>
        </li>
        <li class="contact__item">
          <svg class="contact__icon" viewBox="0 0 16 16" aria-hidden="true"><rect x="1" y="3.5" width="14" height="9" rx="1" fill="#f39422"/><path d="M1.5 4l6.5 5 6.5-5" fill="none" stroke="#fff" stroke-width="1.2"/></svg>
          <span>info@your websitename.com</span>
        </li>
        <li class="contact__item">
          <svg class="contact__icon" viewBox="0 0 16 16" aria-hidden="true"><circle cx="8" cy="8" r="7" fill="#f39422"/><path d="M4 4.5c1.5.5 2 1.8 1.2 3S6 10 7 11M10 3c-.5 1.5.5 2.5 2 2.5M9.5 9.5c1 0 2 1 1.5 2.5" fill="none" stroke="#fff" stroke-width="1.1"/></svg>
          <span>www.your websitename.com</span>
        </li>
      </ul>
    </div>
  </section>

  <section class="card card--back" aria-label="Business card back">
    <div class="pattern-field" role="img" aria-label="Grid of square tiles fading from black to grey across the card"></div>
    <span class="company-name">528BUILDA</span>
  </section>
</main>
</body>
</html>
```